Biz Card Design TVCP

New business card for a new company.
Logo was completed by a designer on ArtHarbor and looking to continue requesting additional services.
Company Name: Tidal Vector Power Consulting
Although this company is starting in Canada, we will be moving towards a global presence within the next 6 months.
Key elements to this business are as follows.
Energy Procurement
Energy Reduction Services
Demand Side Consulting
Energy Efficiency Consulting
Saving Clients Money
Helping Them Go "Green"
Managing Their Energy Requirements
Basically the goal for our company is to find the best procurement solution for our clients and reduce their energy consumption. This reduces their expenses and the amount of greenhouse gas they produce on a daily basis.
I have been in the energy footprint for the last 20 years and know that most companies are looking to "do whatever is necessary to get them to sign on the dotted line". I would prefer to walk away from a client that I can't help than to put them into a situation that they will regret for years to come. This is where the "TIDAL" part of the company name comes from.
The following is a catch phrase that encompasses what we do.
"Reducing your carbon footprint & energy bill at the same time!"
The back of the card needs to have this statement along with some sort of illustration. The back is a playground for creative ideas.
The front of the card needs the following.
Logo.
First & Last Name (Gus Marwick)
Title (Energy Warrior)
Phone Number (555) 314-2718
Fax Number (555) 271-8314
Email Address gus@tidalvectorpowerconsulting.example
Address 47 fenwick rd Toronto Ontario K4T 2P9
I want it to be a card that is remembered when any of my staff give it to a customer. It HAS to stand out.
Target Market(s)
Business Owners, Decision Makers, 30 to 65+
Industry/Entity Type
Business
Look and feel

```html
<!DOCTYPE html>
<html lang="en">
<head>
<meta charset="utf-8">
<title>Tidal Vector Power Consulting — Business Card</title>
<link rel="stylesheet" href="https://fonts.googleapis.com/css2?family=Open+Sans:wght@400;600;700&display=swap">
<style>
  :root {
    --stage: #eef0f2;
    --back-blue: #3d6db6;
    --back-blue-deep: #2f5ca3;
    --back-blue-soft: #4a79c0;
    --brand-blue: #3a62ae;
    --brand-green: #2fa24a;
    --band-green-dark: #0d8a3c;
    --band-green-light: #c6e19a;
    --ink-grey: #6b6b6b;
    --paper: #ffffff;
    --card-shadow: 0 10px 24px rgba(0, 0, 0, 0.18);
  }

  * { box-sizing: border-box; margin: 0; padding: 0; }

  html, body {
    width: 1200px;
    height: 900px;
    overflow: hidden;
  }

  body {
    background: var(--stage);
    font-family: "Open Sans", Arial, sans-serif;
  }

  .stage {
    width: 1200px;
    height: 900px;
    display: flex;
    align-items: center;
    justify-content: center;
    gap: 50px;
  }

  .card {
    position: relative;
    width: 525px;
    height: 300px;
    overflow: hidden;
    box-shadow: var(--card-shadow);
  }

  /* ---------- Back of card ---------- */
  .card-back {
    background: var(--back-blue);
  }

  .card-back .backdrop-art {
    position: absolute;
    inset: 0;
    background:
      radial-gradient(ellipse 60% 75% at 72% 35%, var(--back-blue-soft) 0%, rgba(74, 121, 192, 0) 70%),
      radial-gradient(ellipse 55% 50% at 22% 78%, var(--back-blue-deep) 0%, rgba(47, 92, 163, 0) 70%);
  }

  .card-back .brand-lockup {
    position: absolute;
    left: 0;
    right: 0;
    top: 108px;
    display: flex;
    align-items: center;
    justify-content: center;
    gap: 12px;
  }

  .card-back .brand-dot {
    width: 22px;
    height: 22px;
    border-radius: 50%;
    background: var(--paper);
  }

  .card-back .brand-name {
    color: var(--paper);
    font-weight: 700;
    font-size: 27px;
    letter-spacing: -0.5px;
  }

  .card-back .tagline-bar {
    position: absolute;
    left: 0;
    right: 0;
    bottom: 0;
    height: 40px;
    background: var(--back-blue-deep);
    color: var(--paper);
    font-size: 14px;
    display: flex;
    align-items: center;
    justify-content: flex-end;
    padding-right: 20px;
  }

  /* ---------- Front of card ---------- */
  .card-front {
    background: var(--paper);
  }

  .card-front .brand-lockup {
    position: absolute;
    left: 28px;
    top: 34px;
    display: flex;
    align-items: center;
    gap: 10px;
  }

  .card-front .brand-dot {
    width: 20px;
    height: 20px;
    border-radius: 50%;
    background: var(--brand-green);
  }

  .card-front .brand-name {
    color: var(--brand-blue);
    font-weight: 700;
    font-size: 22px;
    letter-spacing: -0.4px;
  }

  .card-front .person {
    position: absolute;
    left: 28px;
    top: 100px;
  }

  .card-front .person-name {
    color: var(--brand-green);
    font-weight: 700;
    font-size: 21px;
  }

  .card-front .person-title {
    color: var(--brand-blue);
    font-weight: 600;
    font-size: 14px;
  }

  .card-front .person-title::before {
    content: "|";
    margin: 0 6px;
    font-weight: 400;
  }

  .card-front .address {
    margin-top: 6px;
    color: var(--ink-grey);
    font-size: 14px;
    line-height: 1.4;
    font-style: normal;
  }

  .card-front .contact {
    position: absolute;
    right: 28px;
    top: 100px;
    text-align: right;
    font-size: 13px;
    line-height: 1.6;
    color: var(--ink-grey);
    list-style: none;
  }

  .card-front .contact-label {
    color: var(--brand-green);
  }

  .card-front .rule {
    position: absolute;
    left: 0;
    right: 0;
    bottom: 46px;
    height: 4px;
    background: var(--brand-blue);
  }

  .card-front .tagline-band {
    position: absolute;
    left: 0;
    right: 0;
    bottom: 0;
    height: 40px;
    background: linear-gradient(90deg, var(--band-green-light) 0%, var(--brand-green) 55%, var(--band-green-dark) 100%);
    color: var(--paper);
    font-weight: 700;
    font-size: 14px;
    display: flex;
    align-items: center;
    justify-content: flex-end;
    padding-right: 20px;
  }
</style>
</head>
<body>
  <main class="stage">
    <section class="card card-back" aria-label="Business card back">
      <div class="backdrop-art" role="img" aria-label="Large faint brand leaves decoration"></div>
      <div class="brand-lockup">
        <span class="brand-dot"></span>
        <span class="brand-name">Tidal Vector Power Consulting</span>
      </div>
      <p class="tagline-bar">"Reducing your carbon footprint &amp; energy bill at the same time!"</p>
    </section>

    <section class="card card-front" aria-label="Business card front">
      <div class="brand-lockup">
        <span class="brand-dot"></span>
        <span class="brand-name">Tidal Vector Power Consulting</span>
      </div>

      <div class="person">
        <p><span class="person-name">Gus Marwick</span><span class="person-title">Energy Warrior</span></p>
        <address class="address">47 fenwick rd Toronto<br>Ontario K4T 2P9</address>
      </div>

      <ul class="contact">
        <li><span class="contact-label">Phone :</span> (555) 314-2718</li>
        <li><span class="contact-label">Fax :</span> (555) 271-8314</li>
        <li>gus@tidalvectorpowerconsulting.example</li>
      </ul>

      <div class="rule"></div>
      <p class="tagline-band">"Reducing your carbon footprint &amp; energy bill at the same time!"</p>
    </section>
  </main>
</body>
</html>
```